Landing Page / Waitlist

I would like a landing page for people to sign up for a waiting list. The text on the page should include (but is not limited to):
1) Main point: The accounting system you'll love
2) Secondary points:
a. Ruthlessly efficient
b. Quietly intelligent
c. Driven by AI
I've attached a file of our logo

The design should be simple, clean, and innovative - this is an ai company

```html
<!DOCTYPE html>
<html lang="en">
<head>
<meta charset="UTF-8">
<title>LedgerNova — Join the Waitlist</title>
<link href="https://fonts.googleapis.com/css2?family=Nunito:wght@400;600;700;800&display=swap" rel="stylesheet">
<style>
  :root {
    --ink-black: #000000;
    --deep-navy: #03112e;
    --ocean: #0b3a8c;
    --electric: #0b7fe0;
    --cyan: #0fb4f5;
    --card-fill: rgba(6, 40, 110, 0.55);
    --card-line: #13a6f0;
    --brand-grey: #8b8b8d;
    --white: #ffffff;
    --footer-band: rgba(4, 28, 80, 0.7);
  }
  * { box-sizing: border-box; margin: 0; padding: 0; }
  html, body { width: 1200px; height: 802px; overflow: hidden; background: var(--ink-black); }
  body { font-family: "Nunito", sans-serif; color: var(--white); }

  .page { position: relative; width: 1200px; height: 802px; overflow: hidden; }

  .backdrop {
    position: absolute; inset: 0;
    background:
      radial-gradient(ellipse 70% 45% at 50% 100%, rgba(20,150,240,0.55), transparent 70%),
      radial-gradient(ellipse 60% 40% at 15% 80%, rgba(20,110,230,0.45), transparent 70%),
      radial-gradient(ellipse 50% 35% at 90% 75%, rgba(20,120,230,0.45), transparent 70%),
      linear-gradient(180deg, var(--ink-black) 0%, #020b1f 28%, var(--deep-navy) 45%, var(--ocean) 75%, var(--electric) 100%);
  }

  .brand {
    position: absolute; top: 120px; left: 0; width: 100%;
    display: flex; justify-content: center; align-items: center; gap: 14px;
  }
  .brand-mark { width: 34px; height: 34px; background: var(--cyan); }
  .brand-name { font-size: 50px; font-weight: 700; color: var(--brand-grey); letter-spacing: -1px; line-height: 1; }

  .headline {
    position: absolute; top: 254px; left: 0; width: 100%;
    text-align: center; font-size: 45px; font-weight: 800; line-height: 1.2;
  }

  .feature {
    position: absolute; top: 399px; width: 254px; height: 99px;
    border: 1.5px solid var(--card-line); background: var(--card-fill);
  }
  .feature--efficient { left: 164px; }
  .feature--intelligent { left: 473px; }
  .feature--ai { left: 781px; }
  .feature-badge {
    position: absolute; left: 50%; top: 0; width: 64px; height: 64px;
    transform: translate(-50%, -50%) rotate(45deg);
    background: var(--cyan); border-radius: 6px;
  }
  .feature-icon {
    position: absolute; left: 50%; top: 0; width: 44px; height: 44px;
    transform: translate(-50%, -50%);
  }
  .feature-label {
    position: absolute; left: 0; right: 0; top: 50px;
    text-align: center; font-size: 21px; font-weight: 600;
  }

  .waitlist-button {
    position: absolute; left: 466px; top: 562px; width: 268px; height: 64px;
    border-radius: 32px; background: linear-gradient(180deg, #16bdfb, #0aa3ef);
    border: 2px solid rgba(255,255,255,0.55);
    display: flex; align-items: center; padding-left: 34px;
    font-size: 16.5px; font-weight: 800; color: var(--white); text-decoration: none;
  }
  .waitlist-button-dot {
    position: absolute; right: 10px; top: 50%; width: 46px; height: 46px;
    transform: translateY(-50%); border-radius: 50%; background: var(--white);
  }

  .site-footer {
    position: absolute; left: 144px; top: 734px; width: 912px; height: 45px;
    background: var(--footer-band);
    display: flex; justify-content: center; align-items: center;
    font-size: 13px; font-weight: 700;
  }
  .site-footer span.sep { margin: 0 8px; }
</style>
</head>
<body>
<main class="page">
  <div class="backdrop" role="img" aria-label="Glowing blue digital network waves with light points rising from the bottom"></div>

  <div class="brand">
    <span class="brand-mark"></span>
    <span class="brand-name">LedgerNova</span>
  </div>

  <h1 class="headline">The Accounting System You'll Love</h1>

  <section class="feature feature--efficient">
    <span class="feature-badge"></span>
    <svg class="feature-icon" viewBox="0 0 44 44" fill="none" stroke="#fff" stroke-width="2" stroke-linecap="round" stroke-linejoin="round">
      <rect x="6" y="28" width="5" height="9"/><rect x="14" y="23" width="5" height="14"/><rect x="22" y="18" width="5" height="19"/><rect x="30" y="12" width="5" height="25"/>
      <path d="M6 22 L16 14 L24 16 L36 6"/><path d="M31 6 H36 V11"/>
    </svg>
    <p class="feature-label">Ruthlessly Efficient</p>
  </section>

  <section class="feature feature--intelligent">
    <span class="feature-badge"></span>
    <svg class="feature-icon" viewBox="0 0 44 44" fill="none" stroke="#fff" stroke-width="2" stroke-linecap="round" stroke-linejoin="round">
      <path d="M20 8 C12 8 8 13 9 19 C6 22 7 29 12 31 C13 36 18 37 20 35 Z"/>
      <path d="M20 14 H28 M20 22 H32 M20 30 H28"/>
      <circle cx="30" cy="14" r="2"/><circle cx="34" cy="22" r="2"/><circle cx="30" cy="30" r="2"/>
    </svg>
    <p class="feature-label">Quietly Intelligent</p>
  </section>

  <section class="feature feature--ai">
    <span class="feature-badge"></span>
    <svg class="feature-icon" viewBox="0 0 44 44" fill="none" stroke="#fff" stroke-width="2" stroke-linecap="round">
      <rect x="11" y="11" width="22" height="22" rx="2"/>
      <path d="M16 6 V11 M22 6 V11 M28 6 V11 M16 33 V38 M22 33 V38 M28 33 V38 M6 16 H11 M6 22 H11 M6 28 H11 M33 16 H38 M33 22 H38 M33 28 H38"/>
      <text x="22" y="26.5" text-anchor="middle" font-family="Nunito, sans-serif" font-size="11" font-weight="700" fill="#fff" stroke="none">AI</text>
    </svg>
    <p class="feature-label">Driven by AI</p>
  </section>

  <a class="waitlist-button" href="#">JOIN THE WAITLIST<span class="waitlist-button-dot"></span></a>

  <footer class="site-footer">
    <span>© 2025 Companyname.All Rights Reserved</span><span class="sep">|</span><span>Privacy Policy</span><span class="sep">|</span><span>Terms of Use</span>
  </footer>
</main>
</body>
</html>
```